RWT Fittings Ltd Business Cards

We need a business card with our business logo. We provide window and door installations on high-rises in west coast British Colombia, Canada.

I would like my business information and details on one side of the card, and the other side the company name with logo

Target Market(s)

General Contractors

Industry/Entity Type

Construction

Contact Information for Business Card

one side i want my company name and logo in the dark theme logo that i provided

Requirements
Must have
• Marco Peltieri, 16045518293, RWTFittings@mailbox-demo.com, 1407-5194 Linden Row Burnaby BC, V5H 2K9, Owner & Manager

```html
<!DOCTYPE html>
<html lang="en">
<head>
<meta charset="utf-8">
<title>RWT Fittings Ltd Business Cards</title>
<link rel="stylesheet" href="https://fonts.googleapis.com/css2?family=Montserrat:wght@600;700&family=Open+Sans:wght@400;600&display=swap">
<style>
  :root {
    --backdrop: #4a4a4a;
    --card: #1b1b1c;
    --card-back: #19191a;
    --accent: #29a8e0;
    --ink: #ffffff;
    --emboss: #2a2a2b;
  }
  * { margin: 0; padding: 0; box-sizing: border-box; }
  html, body {
    width: 1200px; height: 801px; overflow: hidden;
    background: var(--backdrop);
  }
  .sheet {
    position: relative; width: 1200px; height: 801px;
    display: flex; align-items: center; justify-content: center; gap: 40px;
  }
  .card {
    position: relative; width: 540px; height: 309px;
    overflow: hidden; box-shadow: 0 14px 30px rgba(0,0,0,.35);
  }
  .card--front { background: var(--card); }
  .card--back {
    background: var(--card-back);
    display: flex; align-items: center; justify-content: center;
  }
  .decor-block {
    position: absolute; left: 0; top: 0; width: 150px; height: 150px;
    background: var(--accent);
  }
  .brand {
    position: absolute; right: 30px; top: 46px;
    display: flex; align-items: center; gap: 10px;
  }
  .brand__mark { width: 18px; height: 18px; background: var(--accent); }
  .brand__name {
    font-family: 'Montserrat', sans-serif; font-weight: 600;
    font-size: 26px; color: var(--accent); letter-spacing: .5px;
  }
  .person { position: absolute; left: 40px; right: 22px; top: 164px; }
  .person__row { display: flex; align-items: center; gap: 12px; }
  .person__name {
    font-family: 'Montserrat', sans-serif; font-weight: 700;
    font-size: 22px; color: var(--accent); letter-spacing: .5px;
    white-space: nowrap;
  }
  .divider { flex: 1; height: 1px; background: var(--accent); }
  .person__role {
    font-family: 'Open Sans', sans-serif; font-size: 15px; color: var(--ink);
    margin-top: 2px;
  }
  .side-tab {
    position: absolute; left: 0; top: 214px; width: 16px; height: 38px;
    background: var(--accent);
  }
  .contacts {
    position: absolute; left: 40px; top: 232px; list-style: none;
    font-family: 'Open Sans', sans-serif; font-size: 15px; color: var(--ink);
  }
  .contacts li { display: flex; align-items: center; gap: 8px; line-height: 22px; }
  .contacts svg { width: 12px; height: 12px; fill: var(--accent); flex: none; }
  .address {
    position: absolute; right: 26px; top: 214px; text-align: right;
    font-family: 'Open Sans', sans-serif; font-size: 15px; color: var(--ink);
    line-height: 21px;
  }
  .back-brand { display: flex; align-items: center; gap: 16px; }
  .back-brand__mark { width: 34px; height: 34px; background: var(--emboss); }
  .back-brand__name {
    font-family: 'Montserrat', sans-serif; font-weight: 600;
    font-size: 44px; color: var(--emboss);
  }
</style>
</head>
<body>
<main class="sheet">
  <section class="card card--front">
    <div class="decor-block" role="img" aria-label="Large brand decoration in blue and grey"></div>
    <div class="brand">
      <span class="brand__mark"></span>
      <span class="brand__name">RWT Fittings Ltd</span>
    </div>
    <div class="person">
      <div class="person__row">
        <p class="person__name">MARCO PELTIERI</p>
        <span class="divider"></span>
      </div>
      <p class="person__role">Owner &amp; Manager</p>
    </div>
    <div class="side-tab"></div>
    <ul class="contacts">
      <li><svg viewBox="0 0 24 24"><path d="M6.6 10.8a15 15 0 0 0 6.6 6.6l2.2-2.2a1 1 0 0 1 1-.25 11.4 11.4 0 0 0 3.6.57 1 1 0 0 1 1 1V20a1 1 0 0 1-1 1A17 17 0 0 1 3 4a1 1 0 0 1 1-1h3.5a1 1 0 0 1 1 1c0 1.25.2 2.45.57 3.57a1 1 0 0 1-.25 1z"/></svg>16045518293</li>
      <li><svg viewBox="0 0 24 24"><path d="M2 5h20v14H2zm2 2v.5l8 5 8-5V7z"/></svg>RWTFittings@mailbox-demo.com</li>
      <li><svg viewBox="0 0 24 24"><circle cx="12" cy="12" r="10"/></svg>www.yourwebsite.com</li>
    </ul>
    <p class="address">1407-5194 Linden Row<br>Burnaby BC, V5H 2K9</p>
  </section>

  <section class="card card--back">
    <div class="back-brand">
      <span class="back-brand__mark"></span>
      <span class="back-brand__name">RWT Fittings Ltd</span>
    </div>
  </section>
</main>
</body>
</html>
```